Business card

We need a business card design for our company based in Auckland , New Zealand called 'Ridge + Studio Ltd'. We provide architectural services. We would like to see designs that use the max. three colours (such as white, black, grey) The final design should communicate financial safety and growth."
Also I will provide our company logo. I would like to the logo to be embeded onto our business card.

Target Market(s)

new residential house, alteration & addition & light commericila design & drafting service

Industry/Entity Type

Architecture

Contact Information for Business Card

Company name: ridge + studio Ltd.
Name: Mark Delford
Job title: architectural designer & Design RDP
email address: mark@rplusd.co.nz
mobile number: 02 5163 2290
web site: www.rplusd.co.nz

Requirements
Must have
• My project must have..
• - embeded logo (attached company logo)
• I don't have a bigger version for our company logo, but I have one old one, so you can remove the word from it)
• - insert the attached small BKTW logo & RDP logo
• - creative, simple and clear business card.
• - Max. three colours
Nice to have
• - Here are the samples I would like to share with you: http://www.plimvora.com/blog/minimalistic-business-card-designs/
• I would like to have my business card like one of the creation.
Should not have
• TBA

```html
<!DOCTYPE html>
<html lang="en">
<head>
<meta charset="utf-8">
<title>Ridge + Studio Ltd — Business Card</title>
<link rel="stylesheet" href="https://fonts.googleapis.com/css2?family=PT+Sans+Narrow:wght@400;700&display=swap">
<style>
  :root {
    --ink: #0b0b0b;
    --paper: #ffffff;
    --paper-grey: #e4e4e4;
    --mid-grey: #8f8f8f;
    --soft-grey: #5a5a5a;
    --light-type: #dcdcdc;
    --backdrop: #2e2e2e;
    --type: "PT Sans Narrow", sans-serif;
  }
  * { box-sizing: border-box; margin: 0; padding: 0; }
  html, body {
    width: 1200px; height: 950px; overflow: hidden;
    background: var(--backdrop);
    font-family: var(--type);
  }
  .canvas { position: relative; width: 1200px; height: 950px; }

  .card {
    position: absolute; left: 250px; width: 700px; height: 420px;
    overflow: hidden;
  }

  /* Back of card */
  .card-back {
    top: 45px;
    background: linear-gradient(135deg, #f4f4f4 0%, var(--paper-grey) 60%, #d2d2d2 100%);
    display: flex; align-items: center; justify-content: center; gap: 34px;
  }
  .member-name {
    font-size: 64px; font-weight: 700; color: var(--soft-grey);
    letter-spacing: 1px;
  }
  .member-divider { width: 2px; height: 110px; background: var(--mid-grey); }
  .partner-badge {
    width: 120px; height: 120px; border-radius: 50%;
    background: var(--soft-grey);
  }

  /* Front of card */
  .card-front { top: 485px; background: var(--ink); }
  .front-shape { position: absolute; inset: 0; }
  .brand {
    position: absolute; left: 40px; top: 170px;
    display: flex; align-items: center; gap: 14px;
    color: var(--ink); font-size: 44px; font-weight: 400;
  }
  .brand-dot { width: 26px; height: 26px; border-radius: 50%; background: var(--ink); }

  .details {
    position: absolute; left: 522px; top: 78px; width: 170px;
    color: var(--paper); line-height: 1.2; white-space: nowrap;
  }
  .person-name { font-size: 26px; font-weight: 400; text-transform: uppercase; letter-spacing: 0.5px; }
  .person-title { font-size: 20px; margin-bottom: 24px; }
  .company { font-size: 17px; margin-bottom: 8px; color: var(--light-type); }
  .contact-list { list-style: none; font-size: 17px; color: var(--light-type); }
  .contact-list li { display: flex; align-items: center; gap: 8px; margin-bottom: 6px; }
  .contact-list svg { width: 15px; height: 15px; flex: none; }
</style>
</head>
<body>
<main class="canvas">

  <section class="card card-back" aria-label="Business card back">
    <span class="member-name">BKTW</span>
    <span class="member-divider"></span>
    <span class="partner-badge" role="img" aria-label="Partner badge"></span>
  </section>

  <section class="card card-front" aria-label="Business card front">
    <svg class="front-shape" viewBox="0 0 700 420" aria-hidden="true">
      <circle cx="190" cy="200" r="318" fill="var(--mid-grey)"/>
      <circle cx="190" cy="200" r="312" fill="#cfcfcf"/>
      <circle cx="186" cy="200" r="308" fill="var(--paper)"/>
    </svg>

    <div class="brand">
      <span class="brand-dot"></span>
      <span class="brand-name">ridge + studio</span>
    </div>

    <div class="details">
      <h1 class="person-name">Mark Delford</h1>
      <p class="person-title">architectural designer &amp;<br>Design RDP</p>
      <p class="company">ridge + studio Ltd.</p>
      <ul class="contact-list">
        <li>
          <svg viewBox="0 0 16 16"><rect x="4" y="1" width="8" height="14" rx="1.5" fill="none" stroke="#fff" stroke-width="1.5"/><circle cx="8" cy="12.5" r="0.9" fill="#fff"/></svg>
          02 5163 2290
        </li>
        <li>
          <svg viewBox="0 0 16 16"><rect x="1" y="3.5" width="14" height="9" fill="#fff"/><path d="M1 3.5 8 9l7-5.5" fill="none" stroke="#000" stroke-width="1.2"/></svg>
          mark@rplusd.co.nz
        </li>
        <li>
          <svg viewBox="0 0 16 16"><circle cx="8" cy="8" r="7" fill="#fff"/><ellipse cx="8" cy="8" rx="3" ry="7" fill="none" stroke="#000" stroke-width="1"/><path d="M1 8h14" stroke="#000" stroke-width="1"/></svg>
          www.rplusd.co.nz
        </li>
      </ul>
    </div>
  </section>

</main>
</body>
</html>
```